A unique communication angle to crowdfunding

Looking for a fresh redesign of a crowd funding website that deals in real estate. I already have the content, but am looking to take the design to the next level.

Existing real estate crowd funding sites focus on the real estate. I want to explore communication angle that:
- puts the investor in the centre of the communication: "become a baron"
- highlights the international nature (international properties, international investors)

There's also quite a lot of copy on the site, as we need to explain the service in quite a bit of detail. There's room to reduce the copy and replace with graphics. Could also consider clicking to see different text (see our difference section in http://galleonfairs.com)

The backend of the platform is already being worked on by a specialist crowd funding service provider.

In total there are 5 pages to be designed.

The homepage is really important. Right now it looks quite dated. It doesn't have a great layout. Note there is no mobile version of the website, so the pages need to be seen well on mobile devices. When looking at the brief, refer to the following links too:

current website:
http://pennyduke.com

some revisions made so far:
http://preview.stakeharbor.com/7K3LQ9

Attached are logo files and another file which contained copy for the pages. No need to rework the logo.

Please make sure to use the same copy in the brief on the webpages, to ensure the layouts work. Designers are free to propose images they feel work on the pages.

I would like to see if rather than tweaking the pages, it's possible to come up with a better design concept. If the 5 pages are accepted, there's a chance I'll request an additional 4 pages.
Updates

Please note the font used in the logo is called "harabara" in case you decide to use it in any of the titles, etc.

Please note there is one additional page for which we would like to review designs. Note the page would be a template to be used on all future real estate detail pages. Here is an example of the current design for reference:

http://pennyduke.com/projects/view/14

In total there are 5 page designs required, (homepage + 4)

Thank you

FYI -

Just a quick note to give information from similar UK real estate crowdfunding sites:
http://www.housewalrus.co.uk
http://tiderock.co.uk
https://www.fundquarry.com

Of the above, only tiderock has a nice clean looking landing page. Information is clear and well laid out.

Hi all, just uploaded a new file in the brief. Contains some comments and a website reference. I thought it may help to explain how we could convey international aspect as well as how we could convey images in a more modern way. This is an option you can consider, but its entirely up to you how how answer the brief. Thanks!

Reason: As requested by some designers needing more time to complete their work. Continue to share your work in progress and receive timely feedback before the deadline.

We would like to let you know that we have just shortlisted the best designs. Together with that, we have also passed some detailed feedback to all designers who weren't shortlisted. If we didn't contact you, please let us know. If you haven't submitted a design or are working on revisions, please note these will no longer be taken into account now. We hope you understand that we need to close the project today. Thank you all once again for your great work and design concepts. Here's hoping we meet again on a future design brief. Cheers, pennyduke team.

Target Market(s)

At the moment, only rich are able to buy real estate. With this service, anyone can become a landlord. Target buyers:

Young professionals, looking to diversify from stock market and lower risk
People nearing retirement, looking for stable rental incomes
Retirees - looking to supplement pensions with possibility of capital gains
Parents - looking for a way to save long term for their children (instead of low interest paying bank accounts)

Industry/Entity Type

Communication

Font styles to use
Sans Serif
Other font styles liked:
• harabara

Colors
add136
f5f9eb
959595
000000

Requirements
Must have
• Overall, the site must convey "whoever you are, you too can become a landlord", and that you don't need to be wealthy to invest in real estate. See

Communication should put the investor (or the baron) at the centre. The investor can be any of those described in the target market.

Show the aspirational side of property ownership.

In addition to the investor/baron character, the second main theme is international. No other real estate crowdfunding website highlights this.
Nice to have
• Banner could show different consumer types, to illustrate that the service can appeal to many different profiles. Refer to attached file "home page reference - plainasbread.com" as an example of how this could be done.

Aim to show the international side of the service. Properties around the world, investors around the world.

```html
<!DOCTYPE html>
<html lang="en">
<head>
<meta charset="utf-8">
<title>pennyduke – Build your property portfolio</title>
<link href="https://fonts.googleapis.com/css2?family=Open+Sans:wght@400;600;700&family=Varela+Round&display=swap" rel="stylesheet">
<style>
:root{
  --green:#99c93a;
  --green-dark:#82b02a;
  --tint:#f5f9eb;
  --grey:#959595;
  --text:#555555;
  --ink:#000000;
  --band:#f2f2f2;
  --dark:#3d3d3d;
  --line:#e2e2e2;
  --white:#ffffff;
  --photo:#b4b8b0;
}
*{margin:0;padding:0;box-sizing:border-box}
html,body{width:1200px;height:3000px;overflow:hidden;background:var(--white)}
body{font-family:"Open Sans",Arial,sans-serif;color:var(--text);position:relative}

/* header */
.site-header{position:absolute;top:0;left:0;width:1200px;height:100px;background:var(--white)}
.brand{position:absolute;left:130px;top:30px;display:flex;align-items:center;gap:12px}
.brand-mark{width:30px;height:30px;border-radius:50%;background:var(--green)}
.brand-name{font-family:"Open Sans",sans-serif;font-weight:700;font-size:22px;color:var(--green)}
.social-top{position:absolute;left:620px;top:22px;display:flex;align-items:center;gap:8px;font-size:14px;color:#444}
.social-top .sq{width:34px;height:28px;background:var(--green)}
.social-top .sq.alt{background:#e7e7e7}
.social-top span{margin-right:8px}
.search{position:absolute;left:818px;top:22px;width:252px;height:28px;display:flex}
.search-field{flex:1;background:#f0f0f0;font-size:12px;color:#aaa;padding:6px 12px}
.search-btn{width:38px;background:#555;display:flex;align-items:center;justify-content:center}
.main-nav{position:absolute;right:130px;top:70px;display:flex;gap:26px;font-size:12px;font-weight:600;color:#555;text-transform:uppercase}
.main-nav a{color:inherit;text-decoration:none;padding-bottom:8px}
.main-nav a.active{color:#222;border-bottom:2px solid var(--green)}

/* hero */
.hero{position:absolute;top:100px;left:0;width:1200px;height:400px;background:#7d7a75}
.hero-caption{position:absolute;left:176px;top:162px;width:514px;height:108px;background:rgba(30,30,30,.72);padding:20px 18px}
.hero-caption h1{font-family:"Varela Round",sans-serif;font-weight:400;font-size:27px;color:var(--green);margin-bottom:10px}
.hero-caption p{font-size:15px;color:var(--green)}
.hero-arrow{position:absolute;top:176px;width:48px;height:48px;border-radius:50%;background:rgba(20,20,20,.75);border:2px solid var(--green);display:flex;align-items:center;justify-content:center}
.hero-arrow.prev{left:76px}
.hero-arrow.next{left:1076px}
.hero-dots{position:absolute;left:114px;top:378px;display:flex;gap:6px}
.hero-dots i{width:10px;height:10px;border-radius:50%;background:#bbb}
.hero-dots i.on{background:var(--green)}

/* intro */
.intro{position:absolute;top:500px;left:0;width:1200px;height:314px;text-align:center}
.intro h2{margin-top:48px;font-family:"Varela Round",sans-serif;font-weight:400;font-size:30px;color:var(--green)}
.intro .rule{width:600px;height:1px;background:var(--line);margin:14px auto 20px}
.intro p{font-size:14px;line-height:24px;color:#666;width:800px;margin:0 auto 24px}
.intro b{color:var(--green);font-weight:600}

/* paths */
.paths{position:absolute;top:814px;left:0;width:1200px;height:306px;background:var(--band)}
.path{position:absolute;top:52px;width:380px}
.path.left{left:190px}
.path.right{left:630px}
.path-card{height:150px;background:var(--white);border:1px solid #ddd;display:flex;padding:26px 18px}
.path-icon{width:80px;height:80px;border-radius:50%;background:#4a4a4a;border:3px solid #ccc;flex:none;display:flex;align-items:center;justify-content:center;margin-right:22px}
.path-card h3{font-family:"Varela Round",sans-serif;font-weight:400;font-size:22px;color:var(--green);margin:6px 0 6px}
.path-card p{font-size:13.5px;line-height:24px;color:#666}
.path-btn{margin-top:12px;height:46px;background:var(--green);border-bottom:3px solid var(--green-dark);color:var(--white);font-family:"Varela Round",sans-serif;font-size:20px;display:flex;align-items:center;justify-content:center}

/* projects */
.projects{position:absolute;top:1120px;left:0;width:1200px;height:650px;text-align:center}
.projects h2{margin-top:32px;font-family:"Varela Round",sans-serif;font-weight:400;font-size:22px;color:var(--green)}
.projects .lede{font-size:13.5px;line-height:24px;color:#666;width:620px;margin:12px auto 0}
.projects .lede b{color:var(--green);font-weight:600}
.project-card{position:absolute;top:158px;width:300px;height:430px;border:1px solid #ddd;background:var(--white);text-align:left}
.project-card.lift{box-shadow:0 0 8px rgba(0,0,0,.25)}
.project-photo{height:212px;position:relative;background:var(--photo)}
.tag-price{position:absolute;left:0;top:0;background:var(--green);color:var(--white);font-size:12px;font-weight:600;padding:6px 8px}
.tag-new{position:absolute;left:0;top:30px;background:#4a4a4a;color:var(--green);font-size:10px;font-weight:600;padding:5px 8px}
.project-body{padding:12px 18px 0}
.project-body h3{font-family:"Varela Round",sans-serif;font-weight:400;font-size:16px;color:var(--green);padding-bottom:8px;border-bottom:1px solid var(--line)}
.project-body p{font-size:12.5px;line-height:22px;color:#666;margin-top:8px;padding-bottom:8px;border-bottom:1px solid var(--line)}
.funded{font-size:13px;font-weight:600;color:#444;margin-top:10px}
.bar{margin:6px 0 0 12px;width:250px;height:18px;border:1px solid #bbb;border-radius:4px;background:#f8f8f8;overflow:hidden}
.bar i{display:block;height:100%;background:var(--green);font-style:normal;font-size:11px;font-weight:600;color:#444;text-align:right;padding-right:4px;line-height:16px}
.details{text-align:center;font-size:13.5px;color:#777;margin-top:10px}
.details.hot{color:var(--green);font-weight:600}

/* community */
.community{position:absolute;top:1770px;left:0;width:1200px;height:440px;
  background:radial-gradient(ellipse at 50% 80%,#5c5c5c 0%,#3a3a3a 55%,#2a2a2a 100%);text-align:center}
.community h2{margin-top:56px;font-family:"Varela Round",sans-serif;font-weight:400;font-size:23px;color:var(--green)}
.community .lede{font-size:14px;line-height:24px;color:#9a9a9a;width:660px;margin:10px auto 0}
.stat{position:absolute;top:176px;width:300px;text-align:center}
.stat .mark{height:48px;display:flex;justify-content:center}
.stat strong{display:block;font-size:19px;line-height:24px;color:var(--green);font-weight:600;margin-top:-8px}
.stat span{display:block;font-size:15px;line-height:24px;color:#aaa;margin-top:18px}

/* press */
.press{position:absolute;top:2268px;left:130px;width:940px;height:200px;border:1px solid #ddd}
.press-label{position:absolute;left:390px;top:-10px;width:180px;height:38px;background:var(--green);color:var(--white);font-size:16px;font-weight:600;display:flex;align-items:center;justify-content:center}
.badge{position:absolute;background:#c9c9c9;border-radius:3px}

/* footer */
.footer-bar{position:absolute;top:2512px;left:0;width:1200px;height:74px;background:#464646}
.footer-bar .follow{position:absolute;left:130px;top:24px;display:flex;align-items:center;gap:10px;font-size:17px;color:var(--green)}
.footer-bar .sq{width:36px;height:28px;border:2px solid var(--green)}
.footer-bar .copy{position:absolute;right:130px;top:28px;font-size:13px;color:var(--green)}
.footer-text{position:absolute;top:2586px;left:130px;width:940px;font-size:13.5px;line-height:22px;color:#666}
.footer-text .intro-p{width:600px;margin-top:22px}
.footer-text b{color:var(--green)}
.footer-text p{margin-bottom:22px}
.partner{position:absolute;left:720px;top:20px;font-size:34px;font-weight:400;color:#444}
</style>
</head>
<body>

<header class="site-header">
  <div class="brand"><span class="brand-mark"></span><span class="brand-name">pennyduke</span></div>
  <div class="social-top"><span>Follow us on</span><i class="sq"></i><i class="sq alt"></i></div>
  <div class="search">
    <div class="search-field">Search...</div>
    <div class="search-btn"><svg width="16" height="16" viewBox="0 0 16 16"><circle cx="6.5" cy="6.5" r="4.5" fill="none" stroke="#fff" stroke-width="2"/><line x1="10" y1="10" x2="14" y2="14" stroke="#fff" stroke-width="2"/></svg></div>
  </div>
  <nav class="main-nav">
    <a class="active">Home</a><a>Sign in</a><a>How it works</a><a>Discover a project</a><a>The Baron</a><a>Blog</a><a>Find out more</a>
  </nav>
</header>

<section class="hero" role="img" aria-label="Investor working on a laptop on a rooftop above a city skyline">
  <div class="hero-caption">
    <h1>Build your property portfolio</h1>
    <p>Join our international community. Pool with friends. Share the gains.</p>
  </div>
  <div class="hero-arrow prev"><svg width="16" height="16" viewBox="0 0 16 16"><path d="M10 3 L5 8 L10 13" fill="none" stroke="#99c93a" stroke-width="2.5"/></svg></div>
  <div class="hero-arrow next"><svg width="16" height="16" viewBox="0 0 16 16"><path d="M6 3 L11 8 L6 13" fill="none" stroke="#99c93a" stroke-width="2.5"/></svg></div>
  <div class="hero-dots"><i class="on"></i><i></i><i></i><i></i></div>
</section>

<section class="intro">
  <h2>Reconstructing a property ladder that's strong and fair</h2>
  <div class="rule"></div>
  <p>By harnessing the power of crowds, it's possible to become a landlord in locations around the world. Forget the burden of financing <b>100%</b> of the purchase.</p>
  <p>Leave the day to day management of your property portfolio to us.</p>
  <p>Start with <b>1%</b> in a project and plan your steps to becoming a true baron</p>
</section>

<section class="paths">
  <div class="path left">
    <div class="path-card">
      <div class="path-icon"><svg width="40" height="44" viewBox="0 0 40 44"><rect x="4" y="14" width="12" height="30" fill="#99c93a"/><rect x="18" y="2" width="14" height="42" fill="#99c93a"/><rect x="33" y="22" width="6" height="22" fill="#99c93a"/></svg></div>
      <div><h3>Find properties</h3><p>Sign up to browse the portfolio. Your journey to becoming a real estate baron starts here.</p></div>
    </div>
    <div class="path-btn">Become a member</div>
  </div>
  <div class="path right">
    <div class="path-card">
      <div class="path-icon"><svg width="44" height="44" viewBox="0 0 44 44"><circle cx="22" cy="9" r="6" fill="#99c93a"/><rect x="16" y="17" width="12" height="26" rx="3" fill="#99c93a"/><circle cx="8" cy="14" r="4.5" fill="#99c93a"/><rect x="3" y="20" width="10" height="20" rx="3" fill="#99c93a"/><circle cx="36" cy="14" r="4.5" fill="#99c93a"/><rect x="31" y="20" width="10" height="20" rx="3" fill="#99c93a"/></svg></div>
      <div><h3>Find Buyers</h3><p>Submit a property or development and raise funds from our real estate barons.</p></div>
    </div>
    <div class="path-btn">Submit a property</div>
  </div>
</section>

<section class="projects">
  <h2>Featured Projects</h2>
  <p class="lede">Brief details of new and popular projects. To view full listings, you will be required to sign up and <b>become a member.</b></p>

  <article class="project-card lift" style="left:130px">
    <div class="project-photo" role="img" aria-label="Photo of a red brick family house">
      <span class="tag-price">From GBP 3,600</span><span class="tag-new">New Launch</span>
    </div>
    <div class="project-body">
      <h3>14 Harbour Row LONDON E1</h3>
      <p>Lorem Ipsum is simply dummy text of the printing and typesetting industry. Lorem Ipsum has been the industry's .</p>
      <div class="funded">Funded</div>
      <div class="bar"><i style="width:50%">50%</i></div>
      <div class="details hot">See Project Details</div>
    </div>
  </article>

  <article class="project-card" style="left:450px">
    <div class="project-photo" role="img" aria-label="Photo of a cream suburban house">
      <span class="tag-price">From GBP 3,600</span><span class="tag-new">New Launch</span>
    </div>
    <div class="project-body">
      <h3>14 Harbour Row LONDON E1</h3>
      <p>Lorem Ipsum is simply dummy text of the printing and typesetting industry. Lorem Ipsum has been the industry's .</p>
      <div class="funded">Funded</div>
      <div class="bar"><i style="width:75%">75%</i></div>
      <div class="details">See Project Details</div>
    </div>
  </article>

  <article class="project-card" style="left:770px">
    <div class="project-photo" role="img" aria-label="Photo of a white Mediterranean villa">
      <span class="tag-price">From GBP 3,600</span><span class="tag-new">New Launch</span>
    </div>
    <div class="project-body">
      <h3>14 Harbour Row LONDON E1</h3>
      <p>Lorem Ipsum is simply dummy text of the printing and typesetting industry. Lorem Ipsum has been the industry's .</p>
      <div class="funded">Funded</div>
      <div class="bar"><i style="width:40%">40%</i></div>
      <div class="details">See Project Details</div>
    </div>
  </article>
</section>

<section class="community" role="img" aria-label="Dark aerial view of a city at dusk behind community statistics">
  <h2>Be Part of a Growing International Community</h2>
  <p class="lede">Gain access to new projects in world class cities and join our growing community of international landlords.</p>

  <div class="stat" style="left:140px">
    <div class="mark"><svg width="34" height="48" viewBox="0 0 34 48"><path d="M17 2 C8 2 2 9 2 17 C2 28 17 46 17 46 C17 46 32 28 32 17 C32 9 26 2 17 2 Z" fill="#4f7f86" opacity=".8"/><circle cx="17" cy="17" r="6" fill="#2f3a3c"/></svg></div>
    <strong>3,200 barons<br>in 6 countries</strong>
    <span>A community of international<br>property barons.</span>
  </div>
  <div class="stat" style="left:450px">
    <div class="mark"><svg width="70" height="48" viewBox="0 0 70 48"><circle cx="35" cy="10" r="8" fill="#6a6a6a"/><rect x="26" y="20" width="18" height="26" rx="5" fill="#6a6a6a"/><circle cx="14" cy="16" r="6" fill="#5a5a5a"/><rect x="6" y="24" width="16" height="22" rx="5" fill="#5a5a5a"/><circle cx="56" cy="16" r="6" fill="#5a5a5a"/><rect x="48" y="24" width="16" height="22" rx="5" fill="#5a5a5a"/></svg></div>
    <strong>USD$ 16.2 million</strong>
    <span style="margin-top:42px">Collective buying power of<br>the pennyduke community</span>
  </div>
  <div class="stat" style="left:760px">
    <div class="mark"><svg width="34" height="48" viewBox="0 0 34 48"><path d="M17 2 C8 2 2 9 2 17 C2 28 17 46 17 46 C17 46 32 28 32 17 C32 9 26 2 17 2 Z" fill="#4f7f86" opacity=".8"/><circle cx="17" cy="17" r="6" fill="#2f3a3c"/></svg></div>
    <strong>64 proposals in 6<br>countries</strong>
    <span>Attractive real estate from<br>around the world</span>
  </div>
</section>

<section class="press" aria-label="Featured in">
  <div class="press-label">Featured In</div>
  <i class="badge" style="left:38px;top:62px;width:114px;height:30px"></i>
  <i class="badge" style="left:180px;top:62px;width:114px;height:30px"></i>
  <i class="badge" style="left:324px;top:60px;width:128px;height:34px"></i>
  <i class="badge" style="left:554px;top:64px;width:350px;height:26px"></i>
  <i class="badge" style="left:158px;top:128px;width:62px;height:34px"></i>
  <i class="badge" style="left:260px;top:134px;width:124px;height:22px"></i>
  <i class="badge" style="left:428px;top:126px;width:42px;height:38px"></i>
  <i class="badge" style="left:512px;top:126px;width:70px;height:38px"></i>
  <i class="badge" style="left:610px;top:130px;width:144px;height:30px"></i>
</section>

<footer>
  <div class="footer-bar">
    <div class="follow">Follow us on <i class="sq"></i><i class="sq"></i></div>
    <div class="copy">© pennyduke 2014</div>
  </div>
  <div class="footer-text">
    <div class="partner">Rise VC group</div>
    <p class="intro-p"><b>Penny Duke</b> is part of the Rise VC Group. The Rise VC Group is a worldwide pioneer and leader in the crowd investing, peer to peer and online investment market.</p>
    <p>By accessing this site and any pages thereof, you agree to be bound by the terms and conditions. This website is only suitable, intended and available for professional or sophisticated, or similar investors in other jurisdictions, or those who are members of pennyduke community and familiar with, and willing to, accept the risks associated with private participation. Pennyduke does not endorse any of the projects that appear on this website, nor does it make any recommendations regarding the appropriateness of particular opportunities for any participant. Each potential participant must review and evaluate the projects in his or her own discretion and determine the suitability of participating.</p>
    <p>This website (the "Site") is in every respect unaffiliated with any site to which it links or to any company or entity (and connected projects, investment opportunity or similar) featured on this Site, and is not meant as an endorsement of any of those companies or entities ("third parties"). Furthermore and for the avoidance of doubt, Pennyduke Limited is in no way affiliated with any third parties featured or referenced on this Site. There is no commercial relationship between Pennyduke Limited and such third parties, nor an agency arrangement or similar. If you believe your Content (including third party content) as each such term is defined in our Terms of Service has been reproduced on the Site without permission, please refer to our Terms of Service for information on how to request its removal from the Site.</p>
  </div>
</footer>

</body>
</html>
```